Local fast-growing company in the service sector

We are looking for a modern business card design, which should also appear on our letterheads

Target Market(s)

Private and industrial sectors

Contact Information for Business Card

Vorname Name
Kellberger Str. 18
71399 Buchenau
Tel.: 07146-839214-0
Name@agentur-kvtl.de

Colors
9d9d9d
919191
aaaaaa

Requirements
Must have
• The logo (file) in silver

```html
<!DOCTYPE html>
<html lang="de">
<head>
<meta charset="utf-8">
<title>KVTL Visitenkarte</title>
<link rel="stylesheet" href="https://fonts.googleapis.com/css2?family=Michroma&family=Didact+Gothic&display=swap">
<style>
  :root {
    --page-bg: #d9d4cd;
    --card-bg: #2d2c2b;
    --card-edge: #4a4846;
    --silver: #aaaaaa;
    --silver-light: #c9c6c2;
    --silver-mid: #9d9d9d;
    --accent-rose: #c9a3a3;
  }
  * { margin: 0; padding: 0; box-sizing: border-box; }
  html, body {
    width: 1200px;
    height: 1010px;
    overflow: hidden;
    background: var(--page-bg);
  }
  .canvas {
    position: relative;
    width: 1200px;
    height: 1010px;
  }
  .business-card {
    position: absolute;
    left: 174px;
    top: 282px;
    width: 852px;
    height: 493px;
    background: var(--card-bg);
    border: 1px solid var(--card-edge);
    box-shadow: 0 12px 36px rgba(0,0,0,0.25);
  }
  .brand {
    position: absolute;
    left: 80px;
    top: 100px;
    display: flex;
    flex-direction: column;
  }
  .brand-name {
    font-family: "Michroma", sans-serif;
    font-size: 54px;
    line-height: 1;
    letter-spacing: 2px;
    color: var(--silver-light);
  }
  .brand-web {
    font-family: "Michroma", sans-serif;
    font-size: 18px;
    letter-spacing: 1px;
    color: var(--silver-light);
    margin-top: 10px;
  }
  .contact {
    position: absolute;
    left: 394px;
    top: 296px;
  }
  .person-name {
    font-family: "Michroma", sans-serif;
    font-size: 22px;
    letter-spacing: 3px;
    color: var(--silver-light);
    margin-bottom: 22px;
  }
  .contact-line {
    display: flex;
    align-items: center;
    gap: 20px;
    font-family: "Didact Gothic", sans-serif;
    font-size: 20px;
    letter-spacing: 1px;
    color: var(--silver-light);
    height: 29px;
  }
  .contact-line svg { width: 20px; height: 16px; flex: none; margin-left: 6px; }
  .contact-address {
    font-family: "Didact Gothic", sans-serif;
    font-size: 20px;
    letter-spacing: 1px;
    line-height: 29px;
    margin-top: 3px;
    margin-left: 8px;
    color: var(--accent-rose);
  }
  .contact-address .city { color: var(--silver-light); }
</style>
</head>
<body>
<main class="canvas">
  <section class="business-card">
    <div class="brand">
      <span class="brand-name">KVTL</span>
      <span class="brand-web">agentur-kvtl.de</span>
    </div>
    <div class="contact">
      <p class="person-name">VORNAME NAME</p>
      <p class="contact-line">
        <svg viewBox="0 0 20 16" aria-hidden="true"><path d="M2 5 Q10 0 18 5 L16 7 L13 5.5 L7 5.5 L4 7 Z M5 8 H15 L17 15 H3 Z" fill="var(--accent-rose)"/></svg>
        07146-839214-0
      </p>
      <p class="contact-line">
        <svg viewBox="0 0 20 16" aria-hidden="true"><rect x="1.5" y="2.5" width="17" height="11" fill="none" stroke="var(--accent-rose)" stroke-width="2"/><path d="M2 3 L10 9 L18 3" fill="none" stroke="var(--accent-rose)" stroke-width="2"/></svg>
        Name@agentur-kvtl.de
      </p>
      <p class="contact-address">Kellberger Str. 18 71399 <span class="city">Buchenau</span></p>
    </div>
  </section>
</main>
</body>
</html>
```